KRWB new business card design

We need a business card design for our established business which is Australia wide however based in Melbourne. We are a young team of Financial Planners who specialize in Insurance and Basic super advice for people like us.

We are people who help our clients get things done in a timely and cost effective manner whilst having a good time and a laugh along the way.

We would like this to have a consistent feel with our new e-brochure which i have attached from a color and font perspective.

Industry/Entity Type

Business

Requirements
Must have
• We do not need specific address details rather just the states we are in:

VIC/NSW/QLD/TAS
Nice to have
• Curved edge to mate the brochure

```html
<!DOCTYPE html>
<html lang="en">
<head>
<meta charset="utf-8">
<title>KRWB business card design</title>
<link rel="stylesheet" href="https://fonts.googleapis.com/css2?family=Arimo:ital,wght@0,400;0,700;1,400;1,700&display=swap">
<style>
  :root {
    --green-light: #6cbf4a;
    --green-dark: #00a651;
    --grey-text: #6e6e6e;
    --grey-heading: #7a7a7a;
    --ink: #333333;
    --white: #ffffff;
    --card-black: #161616;
    --backdrop: #e8e5e1;
    --label: #2b2b2b;
  }
  * { box-sizing: border-box; margin: 0; padding: 0; }
  html, body { width: 1200px; height: 788px; overflow: hidden; }
  body {
    position: relative;
    background: var(--backdrop);
    font-family: "Arimo", Arial, sans-serif;
  }
  .side-label {
    position: absolute;
    width: 527px;
    text-align: center;
    font-size: 22px;
    color: var(--label);
  }
  .card {
    position: absolute;
    width: 527px;
    height: 300px;
    border-radius: 22px;
    background: var(--white);
    overflow: hidden;
    box-shadow: 0 4px 10px rgba(0,0,0,0.25);
  }
  .card--front { left: 53px; top: 72px; }
  .card--back1 { left: 622px; top: 74px; }
  .card--back2 { left: 53px; top: 446px; }
  .card--back3 { left: 622px; top: 446px; background: radial-gradient(ellipse at 40% 45%, #2a2a2a 0%, var(--card-black) 70%); }

  .wave { position: absolute; left: 0; top: 0; }

  .brand {
    position: absolute;
    display: flex;
    align-items: center;
    gap: 10px;
    font-weight: 700;
    color: var(--green-dark);
    white-space: nowrap;
  }
  .brand__square { display: block; flex: none; background: var(--green-light); }
  .brand__name { line-height: 1; }

  .front__brand { left: 46px; top: 150px; font-size: 44px; }
  .front__brand .brand__square { width: 40px; height: 40px; }

  .adviser {
    position: absolute;
    right: 34px;
    top: 22px;
    text-align: right;
    color: var(--white);
    font-weight: 700;
  }
  .adviser__name { font-size: 17px; line-height: 20px; }
  .adviser__role { font-size: 13px; line-height: 17px; }

  .contacts {
    position: absolute;
    right: 35px;
    top: 132px;
    list-style: none;
    text-align: right;
    font-size: 14px;
    line-height: 26px;
    color: var(--ink);
  }
  .contacts__key { font-style: italic; font-weight: 700; margin-right: 3px; }

  .specialties-heading {
    font-style: italic;
    font-weight: 700;
    font-size: 18px;
    color: var(--grey-heading);
    margin-bottom: 10px;
  }
  .specialties { list-style: none; font-weight: 700; font-size: 14.5px; line-height: 34px; color: var(--grey-text); }
  .specialties li::before { content: "▪ "; }

  .back1__brand { left: 50px; top: 112px; font-size: 40px; }
  .back1__brand .brand__square { width: 36px; height: 36px; }
  .back1__divider {
    position: absolute; left: 260px; top: 20px; width: 2px; height: 236px;
    background: linear-gradient(to bottom, rgba(0,0,0,0), #8a8a8a 50%, rgba(0,0,0,0));
  }
  .back1__list { position: absolute; left: 320px; top: 44px; }
  .back1__list .specialties { line-height: 34px; margin-top: -2px; }
  .tagline-band {
    position: absolute; left: 0; bottom: 0; width: 100%; height: 39px;
    background: var(--green-light);
    color: var(--white);
    font-weight: 700; font-size: 14px;
    display: flex; align-items: center; justify-content: center;
  }

  .back2__watermark {
    position: absolute; left: 152px; top: 14px; width: 222px; height: 272px;
    border-radius: 18px; background: #eef3ea;
  }
  .back2__list { position: absolute; left: 0; top: 46px; width: 100%; text-align: center; }
  .back2__list .specialties { color: var(--ink); }
  .back2__tagline {
    position: absolute; left: 0; bottom: 16px; width: 100%;
    text-align: center; font-weight: 700; font-size: 14px; color: var(--ink);
  }

  .back3__brand { left: 48px; top: 118px; font-size: 52px; color: var(--white); }
  .back3__brand .brand__square { width: 46px; height: 46px; }
  .back3__list { position: absolute; left: 314px; top: 24px; }
  .back3__list .specialties-heading { color: var(--white); }
  .back3__list .specialties { color: var(--white); }
  .back3__tagline {
    position: absolute; left: 314px; top: 252px;
    color: var(--green-light); font-weight: 700; font-size: 14px; line-height: 18px;
  }
</style>
</head>
<body>
  <div class="side-label" style="left:53px; top:34px;">Front</div>
  <div class="side-label" style="left:622px; top:34px;">Back - 1</div>
  <div class="side-label" style="left:53px; top:404px;">Back - 2</div>
  <div class="side-label" style="left:622px; top:404px;">Back - 3</div>

  <section class="card card--front" aria-label="Card front">
    <svg class="wave" width="527" height="140" viewBox="0 0 527 140" aria-hidden="true">
      <path d="M0,0 H527 V78 C430,108 330,118 250,100 C160,80 70,40 0,42 Z" fill="var(--green-light)"/>
      <path d="M0,45 C70,43 160,83 250,104 C330,122 430,113 527,83 V95 C430,127 330,137 250,123 C160,105 70,62 0,57 Z" fill="var(--green-dark)"/>
    </svg>
    <div class="adviser">
      <p class="adviser__name">Liam Hartwell</p>
      <p class="adviser__role">ADFS, BBus, LRS©</p>
      <p class="adviser__role">Financial Adviser</p>
    </div>
    <div class="brand front__brand">
      <span class="brand__square"></span><span class="brand__name">KRWB</span>
    </div>
    <ul class="contacts">
      <li><span class="contacts__key">c</span>0400 555 218</li>
      <li><span class="contacts__key">p</span>1300 555 014</li>
      <li><span class="contacts__key">f</span>03 9555 0142</li>
      <li><span class="contacts__key">e</span>liam@krwb.com.au</li>
      <li><span class="contacts__key">w</span>www.krwb.com.au</li>
      <li>VIC/NSW/QLD/TAS</li>
    </ul>
  </section>

  <section class="card card--back1" aria-label="Card back, option 1">
    <div class="brand back1__brand">
      <span class="brand__square"></span><span class="brand__name">KRWB</span>
    </div>
    <div class="back1__divider"></div>
    <div class="back1__list">
      <p class="specialties-heading">Specialising in</p>
      <ul class="specialties">
        <li>Risk Insurance</li>
        <li>Debt Management</li>
        <li>Superannuation</li>
        <li>Wealth Creation</li>
        <li>Retirement Planning</li>
      </ul>
    </div>
    <div class="tagline-band">SECURE FUTURE, ENHANCED LIFESTYLE</div>
  </section>

  <section class="card card--back2" aria-label="Card back, option 2">
    <div class="back2__watermark"></div>
    <div class="back2__list">
      <p class="specialties-heading" style="color:var(--ink);">Specialising in</p>
      <ul class="specialties">
        <li>Risk Insurance</li>
        <li>Debt Management</li>
        <li>Superannuation</li>
        <li>Wealth Creation</li>
        <li>Retirement Planning</li>
      </ul>
    </div>
    <p class="back2__tagline">SECURE FUTURE, ENHANCED LIFESTYLE</p>
  </section>

  <section class="card card--back3" aria-label="Card back, option 3">
    <div class="brand back3__brand">
      <span class="brand__square"></span><span class="brand__name">KRWB</span>
    </div>
    <div class="back3__list">
      <p class="specialties-heading">Specialising in</p>
      <ul class="specialties">
        <li>Risk Insurance</li>
        <li>Debt Management</li>
        <li>Superannuation</li>
        <li>Wealth Creation</li>
        <li>Retirement Planning</li>
      </ul>
    </div>
    <p class="back3__tagline">SECURE FUTURE<br>ENHANCED LIFESTYLE</p>
  </section>
</body>
</html>
```